Business Card Design

Brambleford Hearth is the name of my health coaching business. My tag line is "Where good health meets real life." I will be working with clients one-on-one and in groups. My target clients are women "of a certain age" who want to be more comfortable in their own skin. We will work together in a 6-month program. The coaching sessions will take place in my kitchen. I will also be conducting monthly cooking classes and field trips - to farmer's markets, speciality markets etc.. for my clients.
Updates

the business name is Brambleford Hearth - I'm not sure how the p got in there at the end of the name

Thank you

Please include the website - www.bramblefordhearth-example.com and the tag line:

Where good health meets real life on the business card.

Thank you

Please add the phone number to the business card - sorry, I forgot to state that in the original brief

(555) 217-4860

Target Market(s)

Women "of a certain age" who want to be more comfortable in their own skin

Industry/Entity Type

Cooking

Contact Information for Business Card

Brambleford Hearth
Where good health meets real life

Tessa Marlowe
Health Coach
(555) 217-4860

Font styles to use
Serif
Sans Serif

Requirements
Must have
• front & back design
I typical like soft colors - and have tended toward greens over time - I'm open although I would not like bright reds, yellows etc..

```html
<!DOCTYPE html>
<html lang="en">
<head>
<meta charset="utf-8">
<title>Brambleford Hearth – Business Card Colour Options</title>
<link rel="stylesheet" href="https://fonts.googleapis.com/css2?family=Open+Sans:wght@600;700&family=Pathway+Gothic+One&family=Yanone+Kaffeesatz:wght@300;400&display=swap">
<style>
  :root {
    --board-bg: #0b1330;
    --label-ink: #ffffff;
  }
  * { box-sizing: border-box; margin: 0; padding: 0; }
  html, body { width: 1200px; height: 1000px; overflow: hidden; background: var(--board-bg); }
  .board { position: relative; width: 1200px; height: 1000px; }

  .option-label {
    position: absolute; width: 585px; text-align: center;
    font-family: "Pathway Gothic One", "Arial Narrow", sans-serif;
    font-size: 29px; color: var(--label-ink); letter-spacing: .3px;
  }

  .card {
    position: absolute; width: 585px; height: 336px; overflow: hidden;
    background: var(--card-bg); color: var(--ink);
    font-family: "Open Sans", Arial, sans-serif;
  }
  .card--white  { --card-bg:#ffffff; --pattern:#e4e4e4; --ink:#6b6b6b; --tag-bg:#6b6b6b; --tag-ink:#ffffff; }
  .card--brown  { --card-bg:#6c5424; --pattern:#7c6330; --ink:#f4a85c; --tag-bg:#a9621c; --tag-ink:#ffffff; }
  .card--sage   { --card-bg:#6fb163; --pattern:#7cbc70; --ink:#1b5a2d; --tag-bg:#1b5a2d; --tag-ink:#ffffff; }
  .card--forest { --card-bg:#4a7b3b; --pattern:#568846; --ink:#c9e7b6; --tag-bg:#c9e7b6; --tag-ink:#4a7b3b; }

  .kitchen-pattern {
    position: absolute; inset: 0;
    background: linear-gradient(180deg, var(--pattern) 0%, var(--card-bg) 45%, var(--pattern) 100%);
    opacity: .8;
  }

  .name-tag {
    position: absolute; left: 325px; top: 24px; width: 245px; height: 34px;
    background: var(--tag-bg); color: var(--tag-ink);
    font-weight: 700; font-size: 22px; line-height: 34px; text-align: center;
  }
  .role {
    position: absolute; right: 20px; top: 56px;
    font-weight: 600; font-size: 23px;
  }

  .business-name {
    position: absolute; left: 46px; top: 118px; white-space: nowrap;
    font-weight: 600; letter-spacing: -1.5px;
  }
  .business-name .primary { font-size: 54px; }
  .business-name .secondary { font-size: 36px; letter-spacing: 0; margin-left: 6px; }
  .tagline {
    position: absolute; right: 36px; top: 186px;
    font-family: "Yanone Kaffeesatz", "Arial Narrow", sans-serif;
    font-weight: 300; font-size: 20px;
  }

  .contact { position: absolute; top: 262px; text-align: center; }
  .contact--email { left: 18px; width: 180px; }
  .contact--web   { left: 202px; width: 186px; }
  .contact--phone { left: 392px; width: 178px; }
  .contact svg { display: block; margin: 0 auto; width: 34px; height: 30px; }
  .contact .rule { height: 3px; background: var(--ink); margin: 0 0 4px; }
  .contact .value {
    font-family: "Yanone Kaffeesatz", "Arial Narrow", sans-serif;
    font-size: 17px; white-space: nowrap;
  }
  .contact--email .value { font-size: 14.5px; }
  .contact--web .value { font-size: 15px; }
  .contact--phone .value { font-family: "Open Sans", Arial, sans-serif; font-weight: 600; font-size: 17px; }
</style>
</head>
<body>
<main class="board">

  <!-- Row 1 -->
  <p class="option-label" style="left:12px; top:66px;">white and gray</p>
  <p class="option-label" style="left:613px; top:70px;">brown and orange</p>

  <section class="card card--white" style="left:12px; top:106px;">
    <div class="kitchen-pattern" role="img" aria-label="Faint pattern of kitchenware silhouettes: teapot, cutlery, bowls, cups and knives"></div>
    <div class="name-tag">Tessa Marlowe</div>
    <div class="role">Health Coach</div>
    <h2 class="business-name"><span class="primary">Brambleford</span><span class="secondary">Hearth</span></h2>
    <p class="tagline">where good health meets real life</p>
    <div class="contact contact--email">
      <svg viewBox="0 0 34 30" fill="none" stroke="currentColor" stroke-width="1.6"><rect x="6" y="9" width="22" height="15" transform="rotate(-25 17 16)"/><path d="M8 12l10 6 9-10" transform="rotate(-10 17 16)"/></svg>
      <div class="rule"></div><p class="value">tessa@bramblefordhearth-example.com</p>
    </div>
    <div class="contact contact--web">
      <svg viewBox="0 0 34 30" fill="none" stroke="currentColor" stroke-width="1.6"><circle cx="14" cy="14" r="11"/><ellipse cx="14" cy="14" rx="5" ry="11"/><path d="M3 14h22M5 8h18M5 20h18"/><circle cx="24" cy="20" r="4"/><path d="M27 23l5 5"/></svg>
      <div class="rule"></div><p class="value">www.bramblefordhearth-example.com</p>
    </div>
    <div class="contact contact--phone">
      <svg viewBox="0 0 34 30" fill="none" stroke="currentColor" stroke-width="1.8"><rect x="11" y="3" width="12" height="24" rx="2" transform="rotate(-30 17 15)"/><path d="M15 23h4" transform="rotate(-30 17 15)"/></svg>
      <div class="rule"></div><p class="value">(555) 217-4860</p>
    </div>
  </section>

  <section class="card card--brown" style="left:613px; top:106px;">
    <div class="kitchen-pattern" role="img" aria-label="Faint pattern of kitchenware silhouettes: teapot, cutlery, bowls, cups and knives"></div>
    <div class="name-tag">Tessa Marlowe</div>
    <div class="role">Health Coach</div>
    <h2 class="business-name"><span class="primary">Brambleford</span><span class="secondary">Hearth</span></h2>
    <p class="tagline">where good health meets real life</p>
    <div class="contact contact--email">
      <svg viewBox="0 0 34 30" fill="none" stroke="currentColor" stroke-width="1.6"><rect x="6" y="9" width="22" height="15" transform="rotate(-25 17 16)"/><path d="M8 12l10 6 9-10" transform="rotate(-10 17 16)"/></svg>
      <div class="rule"></div><p class="value">tessa@bramblefordhearth-example.com</p>
    </div>
    <div class="contact contact--web">
      <svg viewBox="0 0 34 30" fill="none" stroke="currentColor" stroke-width="1.6"><circle cx="14" cy="14" r="11"/><ellipse cx="14" cy="14" rx="5" ry="11"/><path d="M3 14h22M5 8h18M5 20h18"/><circle cx="24" cy="20" r="4"/><path d="M27 23l5 5"/></svg>
      <div class="rule"></div><p class="value">www.bramblefordhearth-example.com</p>
    </div>
    <div class="contact contact--phone">
      <svg viewBox="0 0 34 30" fill="none" stroke="currentColor" stroke-width="1.8"><rect x="11" y="3" width="12" height="24" rx="2" transform="rotate(-30 17 15)"/><path d="M15 23h4" transform="rotate(-30 17 15)"/></svg>
      <div class="rule"></div><p class="value">(555) 217-4860</p>
    </div>
  </section>

  <!-- Row 2 -->
  <p class="option-label" style="left:12px; top:533px;">sage green and dark green</p>
  <p class="option-label" style="left:650px; top:533px;">dark green and light green (orignal)</p>

  <section class="card card--sage" style="left:12px; top:572px;">
    <div class="kitchen-pattern" role="img" aria-label="Faint pattern of kitchenware silhouettes: teapot, cutlery, bowls, cups and knives"></div>
    <div class="name-tag">Tessa Marlowe</div>
    <div class="role">Health Coach</div>
    <h2 class="business-name"><span class="primary">Brambleford</span><span class="secondary">Hearth</span></h2>
    <p class="tagline">where good health meets real life</p>
    <div class="contact contact--email">
      <svg viewBox="0 0 34 30" fill="none" stroke="currentColor" stroke-width="1.6"><rect x="6" y="9" width="22" height="15" transform="rotate(-25 17 16)"/><path d="M8 12l10 6 9-10" transform="rotate(-10 17 16)"/></svg>
      <div class="rule"></div><p class="value">tessa@bramblefordhearth-example.com</p>
    </div>
    <div class="contact contact--web">
      <svg viewBox="0 0 34 30" fill="none" stroke="currentColor" stroke-width="1.6"><circle cx="14" cy="14" r="11"/><ellipse cx="14" cy="14" rx="5" ry="11"/><path d="M3 14h22M5 8h18M5 20h18"/><circle cx="24" cy="20" r="4"/><path d="M27 23l5 5"/></svg>
      <div class="rule"></div><p class="value">www.bramblefordhearth-example.com</p>
    </div>
    <div class="contact contact--phone">
      <svg viewBox="0 0 34 30" fill="none" stroke="currentColor" stroke-width="1.8"><rect x="11" y="3" width="12" height="24" rx="2" transform="rotate(-30 17 15)"/><path d="M15 23h4" transform="rotate(-30 17 15)"/></svg>
      <div class="rule"></div><p class="value">(555) 217-4860</p>
    </div>
  </section>

  <section class="card card--forest" style="left:615px; top:572px;">
    <div class="kitchen-pattern" role="img" aria-label="Faint pattern of kitchenware silhouettes: teapot, cutlery, bowls, cups and knives"></div>
    <div class="name-tag">Tessa Marlowe</div>
    <div class="role">Health Coach</div>
    <h2 class="business-name"><span class="primary">Brambleford</span><span class="secondary">Hearth</span></h2>
    <p class="tagline">where good health meets real life</p>
    <div class="contact contact--email">
      <svg viewBox="0 0 34 30" fill="none" stroke="currentColor" stroke-width="1.6"><rect x="6" y="9" width="22" height="15" transform="rotate(-25 17 16)"/><path d="M8 12l10 6 9-10" transform="rotate(-10 17 16)"/></svg>
      <div class="rule"></div><p class="value">tessa@bramblefordhearth-example.com</p>
    </div>
    <div class="contact contact--web">
      <svg viewBox="0 0 34 30" fill="none" stroke="currentColor" stroke-width="1.6"><circle cx="14" cy="14" r="11"/><ellipse cx="14" cy="14" rx="5" ry="11"/><path d="M3 14h22M5 8h18M5 20h18"/><circle cx="24" cy="20" r="4"/><path d="M27 23l5 5"/></svg>
      <div class="rule"></div><p class="value">www.bramblefordhearth-example.com</p>
    </div>
    <div class="contact contact--phone">
      <svg viewBox="0 0 34 30" fill="none" stroke="currentColor" stroke-width="1.8"><rect x="11" y="3" width="12" height="24" rx="2" transform="rotate(-30 17 15)"/><path d="M15 23h4" transform="rotate(-30 17 15)"/></svg>
      <div class="rule"></div><p class="value">(555) 217-4860</p>
    </div>
  </section>

</main>
</body>
</html>
```